KVT Web Design Project

I would like a simple and elegant design for my international business consulting practice web site. I already have new KVT Logo and will have brochure-colors are blue, green and black

Practice areas:
I offer consulting services specializing in developing Internet-based anti-counterfeiting and anti-fraud programs, test purchases and investigations.

I offer Cyber Security, Data Protection and Compliance services

I also offer International Due Diligence Investigations and Country and Travel Risk Assessments

General Background Investigations

Physical Security Services

About me section listing my Bio

I have a set of key associates that I work with around the world and will want to list their CVs or Bios under "KVT

Associates"Banner with nice photo but not too cluttered

Ability to Upload documents and articles

Contact us section
Updates

I have uploaded my new logo-please advise if you didn't get it or it is not in the correct file format.

Thank you

Dominic

Hello Everyone,

Thank you for your submissions and ideas. I'm not sure about design only vs code. I understand that some of you do not do code-if not then please just provide design.

More about my business: see below link on Google docs to my brochure-this should help but don't use that phone number-see below.

https://files.quillbin.example/view?id=7Qx2Lm9Pz4Rt8Kw3Hn6Vb1Jc5Fd0Sg

 

Here are some details.

Contacts:

Dominic R. Torvello, CPP

President

Torvello and Associates, LLC

P.O. Box 47129

Gaithersburg, MD 20914

USA

web address:www.Torvelloandassociates.example (currently not working)

email:dom @torvelloand associates.example

Tel: 202-555-0173

I hope this is helpful. Dom

Reason: Sorry but during holiday period, have not had as much time to devote to this project. Thanks for your submissions.

Per my previous guidance, please keep designs simple and elegant and free from traditional security images with locks and chains-I prefer one or at most, two photos. Two colors- blue and green in addition to black for print. I want to present professional, corporate and international image. Thank you for your ideas nad submissions.

Dom

Target Market(s)

Law firms, large multi-national corporations, Security Industry

Industry/Entity Type

Business

Requirements
Must have
• Must have sections: (will provide text)

About KVT (will provide text)

Practice areas

Associates (will provide text)

Contact us

(it must also have ability to upload files and articles)
Should not have
• Old style fonts and symbols such as security badges, scales of justice, etc. I want a sleek and modern design.

```html
<!DOCTYPE html>
<html lang="en">
<head>
<meta charset="utf-8">
<title>Torvello &amp; Associates, LLC</title>
<link href="https://fonts.googleapis.com/css2?family=Arimo:ital,wght@0,400;0,700;1,400&family=Ubuntu:wght@400&display=swap" rel="stylesheet">
<style>
:root{
  --page:#ffffff;
  --band-top:#f4f4f4;
  --band-bottom:#e6e6e6;
  --ink:#222222;
  --brand-blue:#1c5e9e;
  --green:#5b7f2c;
  --body:#555555;
  --navy:#1a2a55;
  --link:#1a9be0;
  --nav-top:#3a3a3a;
  --nav-bottom:#111111;
  --dot:#c8270e;
  --rule:#d6d6d6;
}
*{margin:0;padding:0;box-sizing:border-box}
html,body{width:1200px;height:1151px;overflow:hidden;background:var(--page);font-family:Arimo,Arial,sans-serif}
.canvas{position:relative;width:1200px;height:1151px}
.band{position:absolute;left:0;top:210px;width:1200px;height:262px;background:linear-gradient(var(--band-top),var(--band-bottom));border-bottom:1px solid #dcdcdc}

.brand{position:absolute;left:153px;top:58px}
.brand-name{font-family:Ubuntu,Arial,sans-serif;font-size:31px;color:var(--ink);display:flex;align-items:center;gap:12px}
.brand-mark{width:14px;height:14px;background:var(--brand-blue)}
.brand-tag{margin-top:10px;font-size:19px;letter-spacing:3px;color:var(--brand-blue)}

.nav{position:absolute;left:151px;top:150px;width:886px;height:50px;border-radius:4px;background:linear-gradient(var(--nav-top),var(--nav-bottom));display:flex;align-items:center;padding-left:19px}
.nav a{color:#fff;text-decoration:none;font-size:16px;margin-right:44px}

.hero{position:absolute;left:121px;top:209px;width:950px;height:340px;background:#e8e8e8;border-radius:3px;box-shadow:0 2px 4px rgba(0,0,0,.12)}
.hero-photo{position:absolute;left:6px;top:6px;width:939px;height:328px;background:linear-gradient(100deg,#7f93c4 0%,#aebcdf 45%,#a6b5dc 100%)}
.hero-title{position:absolute;left:485px;top:186px;font-style:italic;font-size:26px;line-height:31px;color:#2a2a2a;text-shadow:1px 1px 0 rgba(255,255,255,.6)}
.hero-dots{position:absolute;right:10px;bottom:14px;display:flex;gap:5px}
.hero-dots span{width:22px;height:22px;border-radius:50%;background:radial-gradient(circle at 40% 35%,#f0583a,var(--dot));border:2px solid #e9e9e9;color:#fff;font-size:12px;display:flex;align-items:center;justify-content:center}

.service{position:absolute;top:613px}
.service h3{font-size:15px;color:var(--green);line-height:18px}
.service p{margin-top:16px;font-size:13px;line-height:15.6px;color:var(--body)}
.service .more{position:absolute;top:120px;font-size:13px;color:var(--link);text-decoration:underline}

.about-title{position:absolute;left:132px;top:774px;font-size:26px;color:var(--green)}
.about-rule{position:absolute;left:123px;top:810px;width:929px;height:1px;background:var(--rule)}
.about-text{position:absolute;left:131px;top:832px;width:665px;font-size:13px;line-height:15.6px;color:var(--navy)}
.about-text p+p{margin-top:0}
.about-text p.gap{margin-top:15.6px}
.about-art{position:absolute;left:809px;top:816px;width:267px;height:195px;background:radial-gradient(circle at 50% 50%,#2ec9e6,#1790c4 70%,#0f6fa6);border:1px solid #0c5f8c}

.footer{position:absolute;left:120px;top:1049px;width:961px;height:110px;border:1px solid #d0d0d0;border-radius:4px;background:linear-gradient(#ffffff,#ececec)}
.footer-nav{position:absolute;top:15px;left:0;width:100%;text-align:center;font-size:11px}
.footer-nav a{color:#111;text-decoration:none;margin:0 14px}
.copyright{position:absolute;top:37px;left:0;width:100%;text-align:center;font-size:12px;color:#2b3a10}
</style>
</head>
<body>
<div class="canvas">
  <div class="band"></div>

  <header class="brand">
    <div class="brand-name"><span class="brand-mark"></span>Torvello &amp; Associates, LLC</div>
    <div class="brand-tag">Intellectual Property and Cyber Security</div>
  </header>

  <nav class="nav">
    <a href="#">Home</a><a href="#">About KVT</a><a href="#">Practice Areas</a><a href="#">Associates</a><a href="#">Contact us</a>
  </nav>

  <section class="hero">
    <div class="hero-photo" role="img" aria-label="Photo of a jubilant businessman with a briefcase breaking a finish-line ribbon against a blue sky"></div>
    <h2 class="hero-title">Secured Your Data From&nbsp; Our<br>Data Protection Services</h2>
    <div class="hero-dots"><span>1</span><span>2</span><span>3</span></div>
  </section>

  <article class="service" style="left:131px;width:195px">
    <h3>Cyber Security</h3>
    <p>Lorem ipsum dolor sit amet, cons ectetur adipiscing elit. Aliqu am tincidunt mi id libero egestas ut interdum nibh cursus.</p>
    <a class="more" href="#" style="left:150px">More &gt;</a>
  </article>
  <article class="service" style="left:364px;width:200px">
    <h3>General Background<br>Investigations</h3>
    <p>Lorem ipsum dolor sit amet, cons ectetur adipiscing elit. Aliqu am tincidunt mi id libero egestas ut interdum nibh cursus.</p>
    <a class="more" href="#" style="left:138px">More &gt;</a>
  </article>
  <article class="service" style="left:607px;width:200px">
    <h3>Data Protection</h3>
    <p>Lorem ipsum dolor sit amet, cons ectetur adipiscing elit. Aliqu am tincidunt mi id libero egestas ut interdum nibh cursus.</p>
    <a class="more" href="#" style="left:140px">More &gt;</a>
  </article>
  <article class="service" style="left:844px;width:200px">
    <h3>Physical Security Services.</h3>
    <p style="line-height:15px">Lorem ipsum dolor sit amet, cons ectetur adipiscing elit. Aliqu am tincidunt mi id libero egestas ut interdum nibh cursus.</p>
    <a class="more" href="#" style="left:157px">More &gt;</a>
  </article>

  <h2 class="about-title">about us</h2>
  <div class="about-rule"></div>
  <div class="about-text">
    <p>Lorem ipsum dolor sit amet, cons ectetur adipiscing elit. Aliqu am tincidunt mi id libero egestas ut interdum nibh cursus. Lorem ipsum dolor sit amet, cons ectetur adipiscing elit. Aliqu am tincidunt mi id libero egestas ut interdum nibh cursus.</p>
    <p>Lorem ipsum dolor sit amet, cons ectetur adipiscing elit. Aliqu am tincidunt mi id libero egestas ut interdum nibh cursus. Lorem ipsum dolor sit amet, cons ectetur adipiscing elit. Aliqu am tincidunt mi id libero egestas ut interdum nibh cursus. Lorem ipsum dolor sit amet, cons ectetur adipiscing elit. Aliqu am tincidunt mi id libero egestas ut interdum nibh cursus.</p>
    <p class="gap">Lorem ipsum dolor sit amet, cons ectetur adipiscing elit. Aliqu am tincidunt mi id libero egestas ut interdum nibh cursus. Lorem ipsum dolor sit amet, cons ectetur adipiscing elit. Aliqu am tincidunt mi id libero egestas ut interdum nibh cursus. Lorem ipsum dolor sit amet, cons ectetur adipiscing elit. Aliqu am tincidunt mi id libero egestas ut</p>
  </div>
  <div class="about-art" role="img" aria-label="Illustration of a glowing globe circled by teal orbit rings on a blue background"></div>

  <footer class="footer">
    <div class="footer-nav"><a href="#">Home</a><a href="#">About KVT</a><a href="#">Practice Areas</a><a href="#">Associates</a><a href="#">Contact us</a></div>
    <div class="copyright">© All right Reserved 2011</div>
  </footer>
</div>
</body>
</html>
```